Spring Detox sale graphics for social media

You MUST read the Brief in the WORD document and follow the instructions there. I want to create 10 social media graphics (new Instagram size 4:5 (1080 x 1350 pixels) focusing on our Mother’s Day Spring Detox Sale graphics, using any of the pics attached. Use the attached pics, NO RANDOM STOCK PHOTOGRAPHY. For the color scheme of the graphics, they should all be complementary to the product colors or feel like Spring time.

Target Market(s)

primarily women

Requirements
Must have
• the photos and text attached

```html
<!DOCTYPE html>
<html lang="en">
<head>
<meta charset="utf-8">
<title>Spring Detox Sale – Social Graphics</title>
<link href="https://fonts.googleapis.com/css2?family=Oswald:wght@300;400;500;600;700&family=Yellowtail&display=swap" rel="stylesheet">
<style>
:root{
  --stage:#5c5c5c;
  --stage-text:#e2e2e2;
  --cream:#f9e8bd;
  --cream-edge:#fdf4de;
  --pink:#d15ea0;
  --purple:#6c3f7c;
  --orange:#d8673a;
  --green:#4f6f34;
  --white:#ffffff;
  --leaf-pink:#c9609a;
  --leaf-purple:#8a4d86;
  --leaf-orange:#d0693f;
}
*{box-sizing:border-box;margin:0;padding:0}
html,body{width:1200px;height:649px;overflow:hidden;background:var(--stage)}
body{position:relative;font-family:"Oswald",sans-serif}
.sheet-title{position:absolute;left:38px;top:26px;font-size:24px;font-weight:500;color:var(--stage-text);letter-spacing:-.2px}
.sheet-size{position:absolute;right:38px;top:28px;font-size:21px;font-weight:300;color:var(--stage-text)}
.post{position:absolute;width:210px;height:263px;border:2px solid var(--cream-edge);overflow:hidden}
.leaf-bg{position:absolute;inset:0;
  background:
   radial-gradient(circle at 8% 30%,rgba(201,96,154,.75),transparent 22%),
   radial-gradient(circle at 95% 25%,rgba(138,77,134,.6),transparent 22%),
   radial-gradient(circle at 10% 85%,rgba(201,96,154,.65),transparent 22%),
   radial-gradient(circle at 92% 80%,rgba(201,96,154,.7),transparent 24%),
   radial-gradient(circle at 50% 4%,rgba(138,77,134,.55),transparent 20%),
   radial-gradient(circle at 50% 98%,rgba(201,96,154,.55),transparent 22%),
   var(--cream)}
.post.warm .leaf-bg{
  background:
   radial-gradient(circle at 8% 30%,rgba(208,105,63,.75),transparent 22%),
   radial-gradient(circle at 95% 25%,rgba(208,105,63,.65),transparent 22%),
   radial-gradient(circle at 10% 85%,rgba(208,105,63,.6),transparent 22%),
   radial-gradient(circle at 92% 80%,rgba(208,105,63,.7),transparent 24%),
   radial-gradient(circle at 50% 4%,rgba(208,105,63,.5),transparent 20%),
   var(--cream)}
.panel{position:absolute;left:22px;top:20px;width:166px;height:223px;
  background-color:var(--cream);
  background-image:linear-gradient(rgba(200,170,120,.12) 1px,transparent 1px),linear-gradient(90deg,rgba(200,170,120,.12) 1px,transparent 1px);
  background-size:4px 4px;
  border:1.5px solid var(--white);box-shadow:0 2px 6px rgba(0,0,0,.25);
  display:flex;flex-direction:column;align-items:center;text-align:center;padding-top:12px;color:var(--pink);line-height:.95}
.offer{font-weight:600;font-size:38px;letter-spacing:-.5px}
.offer.sm{font-size:30px}
.offer.md{font-size:35px}
.everything{font-weight:600;font-size:27px}
.all-supp{font-weight:600;font-size:19px;margin-top:2px}
.mday-arc{font-weight:600;font-size:13px;transform:rotate(8deg);margin-bottom:-6px}
.spark{font-size:9px}
.spring{font-family:"Yellowtail",cursive;font-size:38px;line-height:.9}
.mday-script{font-family:"Yellowtail",cursive;font-size:27px;color:var(--purple);line-height:1;margin-top:6px}
.ribbon{background:var(--purple);color:var(--white);font-weight:600;font-size:12px;letter-spacing:.4px;padding:1px 9px 0;line-height:14px;
  clip-path:polygon(0 0,100% 0,94% 50%,100% 100%,0 100%,6% 50%)}
.ribbon.green{background:var(--green)}
.ribbon.sale{width:114px;display:flex;align-items:center;justify-content:center;gap:6px;font-size:11px;letter-spacing:1.5px;margin-top:-1px}
.ribbon.sale::before,.ribbon.sale::after{content:"";width:24px;height:1px;background:var(--white)}
.tagline{font-weight:500;font-size:17px;margin-top:8px}
.tagline .big{display:block;font-size:22px}
.orange{color:var(--orange)}
.products{margin-top:auto;margin-bottom:16px;width:134px;height:56px;border-radius:3px;
  background:linear-gradient(90deg,#f2f1ef 0 22%,transparent 22% 26%,#f2f1ef 26% 48%,transparent 48% 52%,#f2f1ef 52% 74%,transparent 74% 78%,#f2f1ef 78%);
  box-shadow:inset 0 -14px 0 rgba(160,90,150,.35)}
.products.lg{width:120px;height:68px;margin-bottom:12px}
</style>
</head>
<body>
<h1 class="sheet-title">Spring Detox sale graphics for social media - Sample 02</h1>
<p class="sheet-size">Instagram size 4:5 (1080 x 1350 pixels)</p>

<!-- row one -->
<article class="post" style="left:38px;top:72px">
  <div class="leaf-bg" role="img" aria-label="Pink and purple leaf pattern"></div>
  <div class="panel">
    <p class="mday-arc"><span class="spark">✦</span> Mother's Day</p>
    <p class="spring" style="font-size:36px">Spring</p>
    <p class="ribbon">DETOX SALE</p>
    <p class="offer sm" style="margin-top:12px">25% OFF</p>
    <p class="everything">EVERYTHING!</p>
    <div class="products" role="img" aria-label="Row of four supplement bottles"></div>
  </div>
</article>

<article class="post" style="left:268px;top:72px">
  <div class="leaf-bg" role="img" aria-label="Pink and purple leaf pattern"></div>
  <div class="panel">
    <p class="offer" style="margin-top:14px">25% OFF</p>
    <p class="mday-arc" style="margin-top:10px"><span class="spark">✦</span> Mother's Day</p>
    <p class="spring" style="font-size:40px">Spring</p>
    <p class="ribbon">DETOX SALE</p>
    <div class="products" role="img" aria-label="Row of four supplement bottles"></div>
  </div>
</article>

<article class="post warm" style="left:497px;top:72px">
  <div class="leaf-bg" role="img" aria-label="Orange leaf pattern"></div>
  <div class="panel orange">
    <p class="offer md" style="margin-top:6px">25% OFF</p>
    <p class="all-supp">ALL SUPPLEMENTS <span class="spark">✦</span></p>
    <p class="spring" style="font-size:44px;margin-top:6px">Spring</p>
    <p class="ribbon green" style="font-size:14px;line-height:17px">DETOX SALE</p>
    <div class="products" role="img" aria-label="Row of four supplement bottles"></div>
  </div>
</article>

<article class="post" style="left:727px;top:72px">
  <div class="leaf-bg" role="img" aria-label="Pink and purple leaf pattern"></div>
  <div class="panel">
    <p class="offer md">25% OFF</p>
    <p class="spring" style="font-size:36px">Spring</p>
    <p class="ribbon">DETOX SALE</p>
    <p class="tagline">SPRING RESET.<span class="big">SUMMER READY.</span></p>
    <div class="products lg" role="img" aria-label="Group of four supplement bottles"></div>
  </div>
</article>

<article class="post" style="left:957px;top:72px">
  <div class="leaf-bg" role="img" aria-label="Pink and purple leaf pattern"></div>
  <div class="panel">
    <p class="offer sm">25% OFF</p>
    <p class="everything">EVERYTHING!</p>
    <p class="mday-arc" style="margin-top:12px"><span class="spark">✦</span> Mother's Day</p>
    <p class="spring" style="font-size:36px">Spring</p>
    <p class="ribbon">DETOX SALE</p>
    <div class="products lg" role="img" aria-label="Group of four supplement bottles"></div>
  </div>
</article>

<!-- row two -->
<article class="post" style="left:38px;top:355px">
  <div class="leaf-bg" role="img" aria-label="Pink and purple leaf pattern"></div>
  <div class="panel">
    <p class="offer md" style="margin-top:6px">25% OFF</p>
    <p class="mday-script">Mother's Day</p>
    <p class="ribbon sale">SALE</p>
    <p class="tagline" style="margin-top:12px">FEEL AMAZING<span class="big" style="font-size:26px">AGAIN!</span></p>
    <div class="products lg" role="img" aria-label="Group of four supplement bottles"></div>
  </div>
</article>

<article class="post" style="left:268px;top:355px">
  <div class="leaf-bg" role="img" aria-label="Pink and purple leaf pattern"></div>
  <div class="panel">
    <p class="offer md" style="margin-top:6px">25% OFF</p>
    <p class="mday-script">Mother's Day</p>
    <p class="ribbon sale">SALE</p>
    <p class="tagline" style="margin-top:12px;font-size:21px">REFRESH<span class="big" style="font-size:25px">YOUR BODY</span></p>
    <div class="products lg" role="img" aria-label="Group of four supplement bottles"></div>
  </div>
</article>

<article class="post warm" style="left:497px;top:355px">
  <div class="leaf-bg" role="img" aria-label="Orange leaf pattern"></div>
  <div class="panel orange">
    <p class="offer md">25% OFF</p>
    <p class="spring" style="font-size:37px">Spring</p>
    <p class="ribbon green">DETOX SALE</p>
    <p class="tagline" style="margin-top:10px;font-size:17px">SPRING CLEANSE.<span class="big">SUMMER GLOW.</span></p>
    <div class="products lg" role="img" aria-label="Group of four supplement bottles"></div>
  </div>
</article>

<article class="post" style="left:727px;top:355px">
  <div class="leaf-bg" role="img" aria-label="Pink and purple leaf pattern"></div>
  <div class="panel">
    <p class="offer md" style="margin-top:6px">25% OFF</p>
    <p class="mday-script">Mother's Day</p>
    <p class="ribbon sale">SALE</p>
    <p class="tagline" style="margin-top:14px;font-size:15px">DETOX THIS SPRING.<span class="big" style="font-size:17px">SHINE THIS SUMMER.</span></p>
    <div class="products lg" role="img" aria-label="Group of four supplement bottles"></div>
  </div>
</article>

<article class="post" style="left:957px;top:355px">
  <div class="leaf-bg" role="img" aria-label="Pink and purple leaf pattern"></div>
  <div class="panel">
    <p class="offer md" style="margin-top:6px">25% OFF</p>
    <p class="mday-script">Mother's Day</p>
    <p class="ribbon sale">SALE</p>
    <p class="tagline" style="margin-top:12px;font-size:22px">SPRING DETOX<span class="big" style="font-size:16px">FOR A SUMMER BODY</span></p>
    <div class="products lg" role="img" aria-label="Group of four supplement bottles"></div>
  </div>
</article>
</body>
</html>
```